Local Roofing/Construction company business needs new biz card design

We need a new business card design, current cards are from the start of this operation and generic at best. We are a local Construction Company (General Contractor) with a majority of our work originating from insurance claims-exterior finish work is the main focus (Roofs-Siding-Gutters etc). Heavily involved with homeowners and the low ball offers they receive from insurance company's after a insurable event takes place. I have attached some of our original logo file(s) below.

```html
<!DOCTYPE html>
<html lang="en">
<head>
<meta charset="utf-8">
<title>Ironridge Build — Business Card</title>
<link href="https://fonts.googleapis.com/css2?family=Open+Sans:wght@400;600;700&display=swap" rel="stylesheet">
<style>
  :root {
    --page: #e9e6e1;
    --card: #061c22;
    --card-deep: #04151a;
    --green: #4cbf6a;
    --white: #f2f5f4;
    --sheen: #3a4a4e;
  }
  * { margin: 0; padding: 0; box-sizing: border-box; }
  html, body {
    width: 1200px; height: 780px; overflow: hidden;
    background: var(--page);
    font-family: "Open Sans", sans-serif;
  }
  .canvas {
    position: relative; width: 1200px; height: 780px;
    display: flex; align-items: center; justify-content: center; gap: 40px;
  }
  .card {
    position: relative; width: 540px; height: 309px;
    background: var(--card); overflow: hidden;
    box-shadow: 0 10px 28px rgba(0,0,0,.25);
  }

  /* Front */
  .brand {
    position: absolute; left: 26px; top: 24px; z-index: 2;
    display: flex; align-items: center; gap: 10px;
  }
  .brand-mark { width: 22px; height: 22px; background: var(--green); }
  .brand-name {
    font-weight: 700; font-size: 24px; letter-spacing: .04em;
    color: var(--green); text-transform: uppercase;
  }
  .contact {
    position: absolute; left: 26px; top: 112px; z-index: 2;
    list-style: none; color: var(--white); font-size: 13.5px; line-height: 1.38;
    white-space: nowrap;
  }
  .contact li { display: flex; align-items: center; gap: 7px; }
  .contact .address { padding-left: 18px; }
  .contact svg { width: 11px; height: 11px; flex: none; fill: var(--green); }
  .decor-emblem {
    position: absolute; left: 270px; top: 186px; width: 210px; height: 123px;
    z-index: 1;
    background: linear-gradient(105deg, var(--card-deep) 0%, #0b2328 60%, var(--sheen) 100%);
    opacity: .85;
  }
  .person {
    position: absolute; right: 42px; top: 118px; z-index: 2; text-align: right;
  }
  .person-name { font-weight: 600; font-size: 27px; color: var(--green); line-height: 1.1; }
  .person-role { font-size: 15px; color: var(--white); margin-top: 4px; }
  .accent-tab {
    position: absolute; right: 0; top: 124px; width: 22px; height: 58px;
    background: var(--green); z-index: 2;
  }

  /* Back */
  .pattern-field {
    position: absolute; inset: 0;
    background: linear-gradient(100deg, var(--card-deep) 0%, #0a2228 55%, #39464a 85%, #8d9598 100%);
  }
  .back-brand {
    position: absolute; right: 70px; bottom: 78px;
    display: flex; align-items: center; gap: 7px;
    background: var(--green); padding: 6px 12px; border-radius: 4px;
  }
  .back-brand .brand-mark { width: 12px; height: 12px; background: var(--white); }
  .back-brand .brand-name { font-size: 15px; color: var(--white); }
</style>
</head>
<body>
<main class="canvas">
  <article class="card card-front">
    <div class="brand">
      <span class="brand-mark"></span>
      <span class="brand-name">Ironridge Build</span>
    </div>

    <ul class="contact">
      <li class="address">42 Birch Hollow Rd</li>
      <li class="address">Fairhaven, MO 63011</li>
      <li>
        <svg viewBox="0 0 12 12"><path d="M2.5 1l2 2-1 1.3c.6 1.4 1.8 2.6 3.2 3.2L8 6.5l2 2-1.4 1.8C5 10 2 7 1.7 2.4z"/></svg>
        555-201-4410
      </li>
      <li>
        <svg viewBox="0 0 12 12"><path d="M2.5 1l2 2-1 1.3c.6 1.4 1.8 2.6 3.2 3.2L8 6.5l2 2-1.4 1.8C5 10 2 7 1.7 2.4z"/></svg>
        555-201-7720 (Emergency)
      </li>
      <li>
        <svg viewBox="0 0 12 12"><circle cx="6" cy="6" r="5.2" fill="none" stroke="#4cbf6a" stroke-width="1.3"/><path d="M1 6h10M6 1c-2.4 3-2.4 7 0 10M6 1c2.4 3 2.4 7 0 10" fill="none" stroke="#4cbf6a" stroke-width="1"/></svg>
        www.ironridgebuild.com
      </li>
      <li>
        <svg viewBox="0 0 12 12"><rect x="1" y="2.5" width="10" height="7" rx="1"/><path d="M1.5 3l4.5 3.6L10.5 3" fill="none" stroke="#061c22" stroke-width="1"/></svg>
        office@ironridgebuild.com
      </li>
    </ul>

    <div class="decor-emblem" role="img" aria-label="Large faint embossed company emblem"></div>

    <div class="person">
      <p class="person-name">Dana Holloway</p>
      <p class="person-role">Co-Founder</p>
    </div>
    <span class="accent-tab"></span>
  </article>

  <article class="card card-back">
    <div class="pattern-field" role="img" aria-label="Repeating tiled emblem pattern fading from dark to silver"></div>
    <div class="back-brand">
      <span class="brand-mark"></span>
      <span class="brand-name">Ironridge Build</span>
    </div>
  </article>
</main>
</body>
</html>
```